TV Antenna Installation business needs a unique flyer

We need a simple but effective flyer design for our TV Aerial installation company based in Newcastle, NSW, Australia called Bright Harbour TV & Aerial Svcs.
We are trying to target areas where there has been a new transmitter installed and most houses just require their aerial redirecting and tv's retuning.

Industry/Entity Type

Business

Requirements
Must have
• We would like the idea of a headline phrase such as " Poor TV reception……..now a thing from the past" or something similar & catchy.
Also "Did you know a new transmitter has been recently installed in your area, we can therefore now GUARANTEE 100% PERFECT PICTURE
Charges from only $95.
- Free 5 year warranty
- Free signal testing
- Free Onsite Quote
Phone 0463 527 209
Nice to have
• Other services include:

- New Installs
- Extra Points & repairs
- TV wall mounting/Home Cinema
- Pull down tall masts

Modern tv picture, see example uploaded

```html
<!DOCTYPE html>
<html lang="en">
<head>
<meta charset="utf-8">
<title>Bright Harbour TV &amp; Aerial Svcs – Flyer</title>
<link href="https://fonts.googleapis.com/css2?family=Nunito:wght@800&family=Comic+Neue:wght@700&family=Archivo+Black&family=Arimo:wght@700&display=swap" rel="stylesheet">
<style>
  :root {
    --cream: #fdfbe9;
    --lime: #bcd63e;
    --leaf: #6cb33f;
    --brand-green: #0a8f3e;
    --red: #c8102e;
    --navy: #2e3192;
    --ink: #231f20;
    --yellow: #fff200;
    --tv-brown: #b8742a;
    --tv-dark: #8a5a2b;
  }
  * { box-sizing: border-box; margin: 0; padding: 0; }
  html, body { width: 871px; height: 1200px; overflow: hidden; background: var(--cream); }
  .flyer { position: relative; width: 871px; height: 1200px; background: var(--cream); font-family: "Arimo", Arial, sans-serif; font-weight: 700; }
  .waves { position: absolute; inset: 0; }
  .brand {
    position: absolute; left: 58px; top: 70px;
    font-family: "Nunito", sans-serif; font-weight: 800; font-size: 34px;
    color: var(--brand-green); letter-spacing: -0.3px;
  }
  .tv-illustration {
    position: absolute; left: 430px; top: 150px; width: 380px; height: 356px;
    background: linear-gradient(160deg, var(--tv-brown), var(--tv-dark));
  }
  .headline { position: absolute; left: 62px; top: 236px; font-family: "Comic Neue", cursive; font-weight: 700; color: var(--red);
    -webkit-text-stroke: 8px #fff; paint-order: stroke fill; }
  .headline-main { font-size: 92px; line-height: 90px; display: block; letter-spacing: 1px; }
  .headline-sub { font-size: 42px; line-height: 44px; display: block; margin: 2px 0 0 42px; }
  .headline-tag { font-size: 44px; line-height: 48px; display: block; margin-top: 24px; }
  .intro {
    position: absolute; left: 0; width: 871px; top: 582px; text-align: center;
    font-size: 27px; line-height: 40px; color: var(--ink);
  }
  .intro .guarantee { color: var(--red); display: block; line-height: 36px; }
  .price {
    position: absolute; left: 0; width: 871px; top: 712px; text-align: center;
    font-family: "Archivo Black", sans-serif; font-size: 38px; color: var(--navy); letter-spacing: 0.5px;
  }
  .price .amount { color: var(--red); font-size: 62px; vertical-align: -4px; margin-left: 6px; }
  .perks {
    position: absolute; left: 380px; top: 797px; width: 438px; height: 217px;
    background: var(--navy); border: 5px solid #8dc63f; border-radius: 70px 40px 40px 60px / 50px 40px 40px 50px;
    display: flex; flex-direction: column; justify-content: center; align-items: center; gap: 16px;
    font-family: "Archivo Black", sans-serif; font-size: 31px; line-height: 36px; color: var(--yellow); list-style: none;
  }
  .services { position: absolute; left: 55px; top: 930px; }
  .services h2 { font-size: 34px; color: #c1272d; margin-bottom: 16px; }
  .services ul { list-style: none; }
  .services li { display: flex; align-items: center; gap: 14px; font-size: 23px; color: var(--navy); height: 36.5px; }
  .services svg { width: 22px; height: 22px; flex: none; }
  .phone {
    position: absolute; left: 468px; top: 1128px; display: flex; align-items: center; gap: 6px;
    font-size: 46px; color: var(--red); letter-spacing: -0.5px;
  }
  .phone svg { width: 42px; height: 42px; }
</style>
</head>
<body>
<main class="flyer">
  <svg class="waves" viewBox="0 0 871 1200" width="871" height="1200" aria-hidden="true">
    <path fill="var(--lime)" d="M0 150 C40 185 120 205 220 198 C330 190 450 172 560 155 L871 160 L871 505 C700 505 520 540 340 545 C220 548 100 530 0 482 Z"/>
    <path fill="var(--leaf)" d="M0 120 C50 170 120 190 220 185 C350 178 450 165 560 155 C450 172 330 190 220 198 C120 205 40 185 0 150 Z"/>
    <path fill="var(--leaf)" d="M330 550 C500 535 700 522 871 558 L871 588 C700 548 500 542 330 550 Z"/>
    <path fill="var(--lime)" d="M400 1200 C550 1130 700 1080 871 1070 L871 1200 Z"/>
    <path fill="var(--leaf)" d="M440 1120 C600 1060 750 1045 871 1042 L871 1064 C740 1068 600 1085 440 1120 Z"/>
  </svg>

  <div class="brand">Bright Harbour TV &amp; Aerial Svcs</div>

  <div class="tv-illustration" role="img" aria-label="Illustration of a retro television with antennas and a signal wave on its screen"></div>

  <h1 class="headline">
    <span class="headline-main">Poor TV</span>
    <span class="headline-sub">reception……..</span>
    <span class="headline-tag">now a thing<br>from the past</span>
  </h1>

  <p class="intro">Did you know a new transmitter has been<br>recently installed in your area, we can therefore now
    <span class="guarantee">GUARANTEE 100% PERFECT PICTURE</span></p>

  <p class="price">Charges from only <span class="amount">$95</span></p>

  <ul class="perks">
    <li>Free 5 year warranty</li>
    <li>Free signal testing</li>
    <li>Free Onsite Quote</li>
  </ul>

  <section class="services">
    <h2>Our services</h2>
    <ul>
      <li><svg viewBox="0 0 22 22"><rect x="2" y="5" width="14" height="14" fill="none" stroke="var(--red)" stroke-width="2"/><path d="M5 11 L9 15 L20 3" fill="none" stroke="var(--red)" stroke-width="2.5"/></svg>New Installs</li>
      <li><svg viewBox="0 0 22 22"><rect x="2" y="5" width="14" height="14" fill="none" stroke="var(--red)" stroke-width="2"/><path d="M5 11 L9 15 L20 3" fill="none" stroke="var(--red)" stroke-width="2.5"/></svg>Extra Points &amp; repairs</li>
      <li><svg viewBox="0 0 22 22"><rect x="2" y="5" width="14" height="14" fill="none" stroke="var(--red)" stroke-width="2"/><path d="M5 11 L9 15 L20 3" fill="none" stroke="var(--red)" stroke-width="2.5"/></svg>TV wall mounting/Home Cinema</li>
      <li><svg viewBox="0 0 22 22"><rect x="2" y="5" width="14" height="14" fill="none" stroke="var(--red)" stroke-width="2"/><path d="M5 11 L9 15 L20 3" fill="none" stroke="var(--red)" stroke-width="2.5"/></svg>Pull down tall masts</li>
    </ul>
  </section>

  <p class="phone">
    <svg viewBox="0 0 42 42" aria-hidden="true"><circle cx="21" cy="21" r="18" fill="none" stroke="var(--navy)" stroke-width="2.5"/><path d="M15 11 C12 13 12 17 14 21 C16 26 20 30 25 31 C28 32 30 30 31 28 L27 24 L24 26 C21 24 19 22 18 19 L20 16 Z" fill="var(--navy)"/></svg>
    0463 527 209
  </p>
</main>
</body>
</html>
```